BrivoTerna. Lantern of the Steady Harvest. Business card

Professional business card for BrivoTerna (Lantern of the Steady Harvest)
My rationale: Strategy-> Execution-> Results-> Value that lead to the BrivoTerna name: We put the Lantern of the Steady Harvest.
We deliver value to our customers helping them at defining a good strategy (cyan arrow). 90% of well formulated strategies fail due to poor execution so we also consider strategical execution very important (green arrow). Due to the execution we obtain the results (blue arrow). Finally, the results provide feedback to redefine strategy, and the new strategy has to be executed and new results obtained providing new feedback and on and on. It's like a wheel that finally, must create corporate value: value for shareholders, staholders, employees, providers...-

Target Market(s)

CEOs and steering comitees , invewrnent funds

Industry/Entity Type

Business Consultant

Contact Information for Business Card

Teodoro Vinsquel
CEO & Founder
teodoro.vinsquel@brivoterna-example.com
Mobile: +34 655.803.912
www.brivoterna-example.com

Colors

Designer to choose colors to be used in the design.

Requirements
Nice to have
• Nice to hace the words: Strategy, execution, results
• Nice to vave the claim: Lantern of the Steady Harvest
• The three colors should be shown:
• cyan for STRATEGY
• green for EXECUTION
• blue for RESULTS
Should not have
• Complete black background

```html
<!DOCTYPE html>
<html lang="en">
<head>
<meta charset="utf-8">
<title>BrivoTerna – Business Card</title>
<link rel="stylesheet" href="https://fonts.googleapis.com/css2?family=Open+Sans:wght@400;600;700&family=Oswald:wght@400;500&display=swap">
<style>
  :root {
    --stage: #2c2e33;
    --paper: #ffffff;
    --brand-blue: #0a3391;
    --strategy-cyan: #00aeef;
    --execution-green: #8cc63f;
    --ink: #2a2a2a;
    --soft-blue: #cdd6ec;
    --soft-green: #e6f0d6;
    --soft-cyan: #cdeefb;
  }
  * { box-sizing: border-box; margin: 0; padding: 0; }
  html, body { width: 1200px; height: 960px; overflow: hidden; }
  body {
    background: var(--stage);
    font-family: "Open Sans", Arial, sans-serif;
    position: relative;
  }
  .card {
    position: absolute;
    width: 640px;
    height: 366px;
    background: var(--paper);
    border-radius: 4px;
    overflow: hidden;
  }
  .card--front { left: 470px; top: 80px; }
  .card--back  { left: 90px;  top: 500px; }

  /* Front */
  .front__brand {
    position: absolute;
    left: 0; right: 0; top: 140px;
    text-align: center;
    font-size: 62px;
    font-weight: 700;
    letter-spacing: -1px;
    color: var(--brand-blue);
  }
  .front__web {
    position: absolute;
    left: 0; right: 0; top: 252px;
    text-align: center;
    font-size: 15px;
    letter-spacing: 3px;
    color: var(--ink);
  }
  .front__web strong { color: var(--brand-blue); font-weight: 600; }

  /* Back */
  .back__brand {
    position: absolute;
    left: 56px; top: 62px;
    font-size: 48px;
    font-weight: 700;
    letter-spacing: -1px;
    color: var(--brand-blue);
  }
  .back__person {
    position: absolute;
    right: 40px; top: 54px;
    text-align: right;
    font-family: "Oswald", "Arial Narrow", sans-serif;
  }
  .back__name { font-size: 24px; font-weight: 500; color: var(--brand-blue); line-height: 1.1; }
  .back__role { font-size: 15px; color: var(--ink); }

  .back__panel {
    position: absolute;
    left: 0; top: 146px;
    width: 384px; height: 220px;
    background: var(--brand-blue);
    border-top-right-radius: 26px;
  }
  .back__accent {
    position: absolute;
    left: 404px; top: 252px;
    width: 236px; height: 114px;
    background: var(--strategy-cyan);
    border-top-left-radius: 22px;
  }
  .back__decor {
    position: absolute;
    left: 404px; top: 150px;
    width: 220px; height: 90px;
    border-radius: 10px;
    background: linear-gradient(180deg, var(--soft-blue) 0%, var(--soft-green) 55%, var(--soft-cyan) 100%);
  }
  .contact {
    position: absolute;
    left: 28px; top: 168px;
    list-style: none;
    color: var(--paper);
    font-size: 14px;
  }
  .contact__item { display: flex; align-items: center; gap: 12px; height: 26px; }
  .contact__icon { width: 14px; height: 14px; flex: none; }
</style>
</head>
<body>

  <section class="card card--front" aria-label="Business card front">
    <div class="front__brand">BrivoTerna</div>
    <div class="front__web">www.<strong>brivoterna-example</strong>.com</div>
  </section>

  <section class="card card--back" aria-label="Business card back">
    <div class="back__brand">BrivoTerna</div>

    <div class="back__person">
      <div class="back__name">Teodoro Vinsquel</div>
      <div class="back__role">CEO &amp; Founder</div>
    </div>

    <div class="back__panel"></div>
    <div class="back__decor" role="img" aria-label="Faint large brand symbol decoration in pale blue, green and cyan"></div>
    <div class="back__accent"></div>

    <ul class="contact">
      <li class="contact__item">
        <svg class="contact__icon" viewBox="0 0 14 14" fill="none" stroke="currentColor" stroke-width="1.4">
          <rect x="3" y="1" width="8" height="12" rx="1.5"/><line x1="6" y1="11" x2="8" y2="11"/>
        </svg>
        <span>+34 655.803.912</span>
      </li>
      <li class="contact__item">
        <svg class="contact__icon" viewBox="0 0 14 14" fill="none" stroke="currentColor" stroke-width="1.4">
          <rect x="1" y="3" width="12" height="8" rx="1"/><polyline points="1,3 7,8 13,3"/>
        </svg>
        <span>teodoro.vinsquel@brivoterna-example.com</span>
      </li>
      <li class="contact__item">
        <svg class="contact__icon" viewBox="0 0 14 14" fill="none" stroke="currentColor" stroke-width="1.2">
          <circle cx="7" cy="7" r="6"/><ellipse cx="7" cy="7" rx="2.6" ry="6"/><line x1="1" y1="7" x2="13" y2="7"/>
        </svg>
        <span>www.brivoterna-example.com</span>
      </li>
    </ul>
  </section>

</body>
</html>
```